We need a business card design for a new company located in Missouri City, TX, entitled 'BrightPath Chiropractic & Holistic Center'. Our services include restoration of health and vitality, spinal exam, health assessment, dietary & fitness programs, lymphatic & therapeutic massage, detox & remineralize body wraps, far infrared sauna therapy

Industry/Entity Type

Business

Contact Information for Business Card

BrightPath Chiropractic & Holistic Center, Marlene Okafor LMT, 4215 Elm Ridge Rd., Suite 310, Missouri City, TX 77482, 281-555-0193

```html
<!DOCTYPE html>
<html lang="en">
<head>
<meta charset="utf-8">
<title>BrightPath Chiropractic &amp; Holistic Center — Business Card</title>
<link rel="stylesheet" href="https://fonts.googleapis.com/css2?family=Open+Sans:wght@400;600&family=Lora:wght@400&display=swap">
<style>
  :root {
    --page-bg: #e9e6e1;
    --card-white: #ffffff;
    --card-shade: #ececec;
    --rose: #e86bb8;
    --rose-soft: #f3a9d4;
    --lime: #a9cc3c;
    --ink: #2b2b2b;
    --ink-muted: #444444;
  }
  * { box-sizing: border-box; margin: 0; padding: 0; }
  html, body { width: 1200px; height: 780px; overflow: hidden; }
  body {
    background: var(--page-bg);
    display: flex;
    align-items: center;
    justify-content: center;
    gap: 50px;
  }
  .card {
    position: relative;
    width: 540px;
    height: 310px;
    border-radius: 18px;
    background: linear-gradient(135deg, var(--card-white) 0%, var(--card-white) 55%, var(--card-shade) 100%);
    box-shadow: 0 4px 14px rgba(0,0,0,0.18);
    overflow: hidden;
  }

  /* brand name */
  .brand__name {
    font-family: "Open Sans", sans-serif;
    font-weight: 600;
    color: var(--rose);
    font-size: 17px;
    line-height: 1.3;
  }

  /* front */
  .card--front .brand {
    position: absolute;
    left: 30px;
    top: 50%;
    transform: translateY(-50%);
    width: 230px;
    text-align: center;
  }
  .card--front .divider {
    position: absolute;
    left: 282px;
    top: 36px;
    bottom: 36px;
    width: 1.5px;
    background: var(--rose-soft);
  }
  .contact {
    position: absolute;
    left: 306px;
    top: 44px;
    right: 20px;
  }
  .contact__name {
    font-family: "Open Sans", sans-serif;
    font-weight: 600;
    color: var(--rose);
    font-size: 19px;
    line-height: 1.2;
  }
  .contact__title {
    font-family: "Lora", serif;
    color: var(--ink);
    font-size: 13px;
    margin-bottom: 24px;
  }
  .contact__line {
    font-family: "Lora", serif;
    color: var(--ink-muted);
    font-size: 12.5px;
    line-height: 1.6;
    display: flex;
    align-items: center;
    gap: 7px;
  }
  .contact__icon {
    flex: none;
    width: 15px;
    height: 15px;
    border-radius: 3px;
    background: var(--lime);
    display: inline-flex;
    align-items: center;
    justify-content: center;
  }
  .contact__address { margin-bottom: 2px; }

  /* back */
  .services {
    position: absolute;
    left: 34px;
    top: 30px;
  }
  .services__heading {
    font-family: "Open Sans", sans-serif;
    font-weight: 600;
    color: var(--rose);
    font-size: 15px;
    letter-spacing: 0.5px;
    margin-bottom: 8px;
  }
  .services__list { list-style: none; }
  .services__item {
    font-family: "Lora", serif;
    color: var(--ink);
    font-size: 13px;
    line-height: 1.62;
    display: flex;
    align-items: center;
    gap: 9px;
  }
  .services__item::before {
    content: "";
    width: 8px;
    height: 8px;
    border-radius: 50%;
    background: var(--rose-soft);
  }
  .card--back .brand {
    position: absolute;
    right: 34px;
    bottom: 34px;
    text-align: right;
  }
</style>
</head>
<body>

  <section class="card card--front" aria-label="Business card front">
    <div class="brand">
      <p class="brand__name">BrightPath Chiropractic<br>&amp; Holistic Center</p>
    </div>
    <span class="divider"></span>
    <div class="contact">
      <p class="contact__name">Marlene Okafor LMT</p>
      <p class="contact__title">Managing Director</p>
      <p class="contact__line contact__address">4215 Elm Ridge Rd., Suite 310,<br>Missouri City, TX 77482</p>
      <p class="contact__line">
        <span class="contact__icon">
          <svg width="9" height="9" viewBox="0 0 24 24"><path fill="#fff" d="M6.6 10.8a15.1 15.1 0 0 0 6.6 6.6l2.2-2.2c.3-.3.7-.4 1-.2 1.1.4 2.3.6 3.6.6.6 0 1 .4 1 1V20c0 .6-.4 1-1 1A17 17 0 0 1 3 4c0-.6.4-1 1-1h3.5c.6 0 1 .4 1 1 0 1.3.2 2.5.6 3.6.1.3 0 .7-.2 1z"/></svg>
        </span>
        281-555-0193
      </p>
      <p class="contact__line">
        <span class="contact__icon">
          <svg width="9" height="9" viewBox="0 0 24 24"><path fill="#fff" d="M2 5h20v14H2z"/><path fill="none" stroke="#a9cc3c" stroke-width="2" d="M2 5l10 8 10-8"/></svg>
        </span>
        hello@brightpathholistic.com
      </p>
    </div>
  </section>

  <section class="card card--back" aria-label="Business card back">
    <div class="services">
      <h2 class="services__heading">OUR SERVICES</h2>
      <ul class="services__list">
        <li class="services__item">restoration of health and vitality</li>
        <li class="services__item">spinal exam</li>
        <li class="services__item">health assessment</li>
        <li class="services__item">dietary &amp; fitness programs</li>
        <li class="services__item">lymphatic &amp; therapeutic massage</li>
        <li class="services__item">detox &amp; remineralize body wraps</li>
        <li class="services__item">far infrared sauna therapy</li>
      </ul>
    </div>
    <div class="brand">
      <p class="brand__name">BrightPath Chiropractic<br>&amp; Holistic Center</p>
    </div>
  </section>

</body>
</html>
```